Business Card Design

We are a company that provides stump grinding services for residential and commercial clients. Looking for a simple business card design that may have some type of graphic on the card that will tie in with the Tamsen name(Grizzly Bear, Paw Print, etc) . Possibly some foliage wrapping around part of the card? Would like to have a simple design that stands out because it is unique. We are working on getting the website set up and there is a simple graphic on the top of the page that came to mind when I mentioned the leaves.

Industry/Entity Type

Business

Contact Information for Business Card

Tamsen Stump Grinding 303-257-4788KodiakStumps.Com

Font styles to use
Serif

Requirements
Must have
• Business name
• Website Address
• Phone Number
Nice to have
• Graphics that would be associated with a Tamsen bear.
Should not have
• Nothing frilly

```html
<!DOCTYPE html>
<html lang="en">
<head>
<meta charset="utf-8">
<title>Tamsen Stump Grinding – Business Card</title>
<link rel="stylesheet" href="https://fonts.googleapis.com/css2?family=Lato:wght@400;700&display=swap">
<style>
  :root {
    --backdrop: #d9d9d7;
    --card-white: #ffffff;
    --brand-blue: #3f7cc6;
    --blue-light: #6aa4da;
    --blue-deep: #3a6fbd;
    --grey-light: #707070;
    --grey-dark: #3b3b3b;
    --ink-white: #ffffff;
  }
  * { box-sizing: border-box; margin: 0; padding: 0; }
  html, body {
    width: 1200px;
    height: 900px;
    overflow: hidden;
    background: var(--backdrop);
    font-family: "Lato", "Helvetica Neue", Arial, sans-serif;
  }
  .canvas {
    position: relative;
    width: 1200px;
    height: 900px;
  }
  .card {
    position: absolute;
    width: 630px;
    height: 360px;
    overflow: hidden;
    box-shadow: 0 6px 18px rgba(0,0,0,0.18);
  }

  /* Front face */
  .card-front {
    left: 440px;
    top: 50px;
    background: var(--card-white);
  }
  .front-lockup {
    position: absolute;
    left: 110px;
    top: 128px;
    display: flex;
    align-items: center;
    gap: 22px;
  }
  .brand-dot {
    width: 96px;
    height: 96px;
    border-radius: 50%;
    background: var(--brand-blue);
    flex: none;
  }
  .brand-name {
    color: var(--brand-blue);
    font-weight: 400;
    line-height: 1.15;
  }
  .brand-name .line-main {
    display: block;
    font-size: 34px;
    letter-spacing: 1px;
  }
  .brand-name .line-sub {
    display: block;
    font-size: 22px;
    letter-spacing: 20px;
    margin-top: 6px;
  }

  /* Back face */
  .card-back {
    left: 150px;
    top: 480px;
  }
  .card-back .back-art {
    position: absolute;
    inset: 0;
    width: 100%;
    height: 100%;
  }
  .back-mark {
    position: absolute;
    left: 58px;
    top: 62px;
    width: 200px;
    height: 200px;
    border: 7px solid var(--ink-white);
    border-radius: 50%;
    display: flex;
    align-items: center;
    justify-content: center;
    text-align: center;
    color: var(--ink-white);
    font-size: 24px;
    font-weight: 400;
    line-height: 1.2;
    letter-spacing: 1px;
  }
  .contact {
    position: absolute;
    right: 52px;
    top: 150px;
    list-style: none;
    color: var(--ink-white);
    font-size: 21px;
    line-height: 1.3;
    text-align: right;
  }
  .contact li {
    display: flex;
    align-items: center;
    justify-content: flex-end;
    gap: 10px;
  }
  .contact svg {
    width: 16px;
    height: 16px;
    fill: none;
    stroke: var(--ink-white);
    stroke-width: 2;
  }
</style>
</head>
<body>
<main class="canvas">

  <section class="card card-front" aria-label="Business card front">
    <div class="front-lockup">
      <span class="brand-dot" aria-hidden="true"></span>
      <h1 class="brand-name">
        <span class="line-main">TAMSEN STUMP</span>
        <span class="line-sub">GRINDING</span>
      </h1>
    </div>
  </section>

  <section class="card card-back" aria-label="Business card back">
    <svg class="back-art" viewBox="0 0 630 360" preserveAspectRatio="none" aria-hidden="true">
      <defs>
        <linearGradient id="greyPanel" x1="0" y1="0" x2="0" y2="1">
          <stop offset="0" stop-color="#7a7a7a"/>
          <stop offset="1" stop-color="#353535"/>
        </linearGradient>
        <linearGradient id="bluePanel" x1="0" y1="0" x2="0" y2="1">
          <stop offset="0" stop-color="#6aa4da"/>
          <stop offset="1" stop-color="#3a6fbd"/>
        </linearGradient>
      </defs>
      <rect width="630" height="360" fill="url(#greyPanel)"/>
      <path d="M238 0 C300 110 285 270 160 360 L210 360 C300 285 330 120 272 0 Z" fill="#ffffff"/>
      <path d="M272 0 L630 0 L630 360 L210 360 C300 285 330 120 272 0 Z" fill="url(#bluePanel)"/>
    </svg>

    <div class="back-mark">Tamsen</div>

    <ul class="contact">
      <li>303-555-0146
        <svg viewBox="0 0 16 16" aria-hidden="true"><path d="M3 2h3l1.5 3.5-2 1.2a8 8 0 0 0 3.8 3.8l1.2-2L14 10v3a1 1 0 0 1-1 1A11 11 0 0 1 2 3a1 1 0 0 1 1-1z"/></svg>
      </li>
      <li>TamsenStumps.Com
        <svg viewBox="0 0 16 16" aria-hidden="true"><path d="M7 9.5a3 3 0 0 0 4.2 0l2.3-2.3a3 3 0 0 0-4.2-4.2L8.4 4"/><path d="M9 6.5a3 3 0 0 0-4.2 0L2.5 8.8a3 3 0 0 0 4.2 4.2l.9-.9"/></svg>
      </li>
    </ul>
  </section>

</main>
</body>
</html>
```